Satchel & Sundial needs new business card design

I need a new business card design. I'm looking for out-of-the-box design which represents the freedom of being a location independent entrepreneur.
I offer coaching, retreats and trips.
I would like to see designs with and without the photo.
Colors I use are black (#000000), green (#25A796) and brown (#D7C38C)
Website satchelandsundial.example

Target Market(s)

location independent entrepreneurs, digital nomads, people looking to swap the 9 to 5 for a lifestyle business

Industry/Entity Type

Business

Contact Information for Business Card

Dorota Falkner
Your Lifestyle Business Coach, Retreat & Trip Leader
http://satchelandsundial.example
hello@satchelandsundial.example
Live a life you don't need a holiday from

Font styles to use
Serif
Sans Serif

Requirements
Must have
• One side should contain only the logo. I would also consider having the "Live a life you don't need a holiday from" on that side too (depending on how it looks)
• Please show both sides on the designs.

```html
<!DOCTYPE html>
<html lang="en">
<head>
<meta charset="utf-8">
<title>Satchel &amp; Sundial — Business Card</title>
<link rel="stylesheet" href="https://fonts.googleapis.com/css2?family=Oswald:wght@400;500;600&display=swap">
<style>
  :root {
    --backdrop: #d9d9d9;
    --card: #f4f4f4;
    --ink: #1a1a1a;
    --green: #25a796;
    --green-deep: #12897a;
    --brown: #d7c38c;
    --white: #ffffff;
  }
  * { box-sizing: border-box; margin: 0; padding: 0; }
  html, body { width: 1200px; height: 576px; overflow: hidden; }
  body {
    background: var(--backdrop);
    font-family: "Oswald", sans-serif;
    color: var(--ink);
    position: relative;
  }
  .card {
    position: absolute;
    top: 139px;
    width: 482px;
    height: 292px;
    background: var(--card);
    border-radius: 6px;
    overflow: hidden;
  }
  .card--front { left: 82px; }
  .card--back { left: 602px; }

  .wordmark {
    font-weight: 500;
    text-transform: uppercase;
    letter-spacing: 0.02em;
    color: var(--ink);
    white-space: nowrap;
    display: flex;
    align-items: center;
    gap: 10px;
  }
  .wordmark__dot {
    width: 12px; height: 12px; border-radius: 50%;
    background: var(--green);
    flex: none;
  }
  .card--front .wordmark {
    position: absolute;
    left: 50%; top: 50%;
    transform: translate(-50%, -50%);
    font-size: 40px;
  }
  .card--back .wordmark {
    position: absolute;
    left: 22px; top: 58px;
    font-size: 30px;
  }

  .holder {
    position: absolute;
    right: 21px; top: 150px;
    text-align: right;
  }
  .holder__name {
    font-size: 19px;
    font-weight: 600;
    text-transform: uppercase;
    letter-spacing: 0.01em;
    line-height: 1.2;
  }
  .holder__role {
    font-size: 11.5px;
    color: var(--green-deep);
    line-height: 1.4;
  }
  .rule {
    position: absolute;
    left: 22px; top: 188px;
    width: 190px; height: 1px;
    background: var(--brown);
  }

  .contacts {
    position: absolute;
    left: 22px; top: 211px;
    list-style: none;
    font-size: 11.5px;
  }
  .contacts li {
    display: flex; align-items: center; gap: 12px;
    height: 21px;
  }
  .contacts svg { width: 11px; height: 11px; fill: var(--green-deep); flex: none; }
  .contacts .accent { color: var(--green-deep); }

  .social {
    position: absolute;
    right: 21px; top: 221px;
    display: flex; align-items: center; gap: 6px;
    font-size: 12px;
    color: var(--green-deep);
  }
  .social__mark { width: 10px; height: 10px; background: var(--ink); border-radius: 2px; }

  .footer-band { position: absolute; left: 0; bottom: 0; width: 482px; height: 37px; }
  .tagline {
    position: absolute;
    right: 21px; bottom: 10px;
    font-size: 13.5px;
    color: var(--white);
    letter-spacing: 0.01em;
  }
</style>
</head>
<body>

  <section class="card card--front" aria-label="Card front">
    <div class="wordmark"><span class="wordmark__dot"></span>Satchel &amp; Sundial</div>
  </section>

  <section class="card card--back" aria-label="Card back">
    <div class="wordmark"><span class="wordmark__dot"></span>Satchel &amp; Sundial</div>

    <div class="holder">
      <p class="holder__name">Dorota Falkner</p>
      <p class="holder__role">Your Lifestyle Business Coach, Retreat &amp; Trip Leader</p>
    </div>

    <div class="rule"></div>

    <ul class="contacts">
      <li>
        <svg viewBox="0 0 12 12"><path d="M0 2h12v8H0z M0 2l6 4.5L12 2" fill="none" stroke="currentColor"/><path d="M0 2h12v8H0V2zm1 1.2V9h10V3.2L6 7 1 3.2z"/></svg>
        <span>hello@satchelandsundial.example</span>
      </li>
      <li>
        <svg viewBox="0 0 12 12"><circle cx="6" cy="6" r="5.3" fill="none" stroke="#12897a" stroke-width="1.1"/><ellipse cx="6" cy="6" rx="2.2" ry="5.3" fill="none" stroke="#12897a" stroke-width="1"/><path d="M0.8 6h10.4" stroke="#12897a" stroke-width="1"/></svg>
        <span>www.<span class="accent">satchelandsundial</span>.example</span>
      </li>
    </ul>

    <div class="social">
      <span class="social__mark"></span>
      <span>/satchelandsundial</span>
    </div>

    <svg class="footer-band" viewBox="0 0 482 37" preserveAspectRatio="none" aria-hidden="true">
      <rect x="0" y="18" width="240" height="19" fill="var(--green-deep)"/>
      <polygon points="226,0 482,0 482,37 212,37" fill="var(--ink)"/>
    </svg>
    <p class="tagline">Live a life you don't need a holiday from</p>
  </section>

</body>
</html>
```